Business Card Design Project - 2 sided

We need a business card design for a card having one business on each side (ie. two businesses on one card). Would like a design that incorporates logo, tagline and normal fields (name, position, address, phone).

Would also like an allowance for small font text along the bottom (text to be determined, but less than 50 characters).

NB. Attached logo for Harbor Quill has two variations - either can be used.

www.harborquill-example.com / www.velmaro-example.com

```html
<!DOCTYPE html>
<html lang="en">
<head>
<meta charset="utf-8">
<title>Harbor Quill / Velmaro – Two-Sided Business Card</title>
<link href="https://fonts.googleapis.com/css2?family=Source+Sans+3:wght@400;600;700&display=swap" rel="stylesheet">
<style>
  :root {
    --bg: #ece9e4;
    --card: #ffffff;
    --green: #8cc63f;
    --grey: #6d6e71;
    --navy: #2e3a7c;
    --blue: #2f87c5;
    --text: #4d4d4f;
    --muted: #58595b;
  }
  * { margin: 0; padding: 0; box-sizing: border-box; }
  html, body { width: 1200px; height: 487px; overflow: hidden; }
  body {
    background: var(--bg);
    font-family: "Source Sans 3", "Helvetica Neue", Arial, sans-serif;
    position: relative;
  }
  .card {
    position: absolute;
    top: 90px;
    width: 544px;
    height: 308px;
    background: var(--card);
    box-shadow: 0 2px 6px rgba(0,0,0,0.18);
  }
  .card--harbor { left: 42px; }
  .card--velmaro { left: 615px; }

  .brand {
    position: absolute;
    left: 0;
    width: 300px;
    text-align: center;
  }
  .card--harbor .brand { top: 138px; }
  .card--velmaro .brand { top: 112px; }
  .brand__name {
    font-weight: 600;
    font-size: 27px;
    line-height: 1;
    letter-spacing: 0.5px;
  }
  .card--harbor .brand__name { color: var(--navy); }
  .card--velmaro .brand__name { color: var(--blue); }
  .brand__tagline {
    margin-top: 7px;
    font-size: 11px;
    color: var(--muted);
  }
  .card--velmaro .brand__tagline { letter-spacing: 1px; font-size: 11.5px; }

  .details {
    position: absolute;
    left: 317px;
    top: 52px;
    color: var(--text);
  }
  .person { font-size: 18px; line-height: 1; margin-bottom: 27px; }
  .person__name { color: var(--green); font-weight: 700; }
  .person__title { color: var(--muted); font-size: 14px; }
  .person__sep { color: var(--green); font-size: 14px; margin: 0 3px; }

  .contacts { list-style: none; font-size: 14px; }
  .contacts li {
    display: flex; align-items: center; gap: 6px;
    height: 18px;
  }
  .contacts svg { width: 11px; height: 11px; fill: var(--green); flex: none; }
  .address { margin-top: 15px; font-size: 14px; line-height: 18px; }

  .bands {
    position: absolute;
    top: 257px; left: 0; right: 0;
    height: 14px;
    display: flex; gap: 5px;
  }
  .bands__primary { width: 313px; background: var(--green); }
  .bands__secondary { flex: 1; background: var(--grey); }
  .card--velmaro .bands__secondary { background: var(--blue); }

  .footnote {
    position: absolute;
    top: 279px; left: 0; width: 100%;
    text-align: center;
    font-size: 14.5px;
    line-height: 18px;
    color: var(--muted);
  }
</style>
</head>
<body>

<svg width="0" height="0" style="position:absolute" aria-hidden="true">
  <defs>
    <symbol id="icon-phone" viewBox="0 0 12 12"><circle cx="6" cy="6" r="6"/><path d="M3.5 3.2l1.3-.6.9 1.6-.8.7c.4.9 1 1.5 1.9 1.9l.7-.8 1.6.9-.6 1.3C6 8.4 3.6 6 3.5 3.2z" fill="#fff"/></symbol>
    <symbol id="icon-mobile" viewBox="0 0 12 12"><rect x="2.5" y="0" width="7" height="12" rx="1.2"/><rect x="3.7" y="1.5" width="4.6" height="7" fill="#fff"/></symbol>
    <symbol id="icon-fax" viewBox="0 0 12 12"><path d="M1 4h10v5H1z"/><path d="M3 1h6v3H3zM3 8h6v3H3z"/><rect x="3.8" y="9" width="4.4" height="1.2" fill="#fff"/></symbol>
    <symbol id="icon-mail" viewBox="0 0 12 12"><rect x="0" y="2" width="12" height="8" rx="1"/><path d="M1 3l5 4 5-4" stroke="#fff" stroke-width="1" fill="none"/></symbol>
    <symbol id="icon-web" viewBox="0 0 12 12"><circle cx="6" cy="6" r="6"/><path d="M0.5 6h11M6 .5c-2.5 3-2.5 8 0 11M6 .5c2.5 3 2.5 8 0 11" stroke="#fff" stroke-width=".8" fill="none"/></symbol>
  </defs>
</svg>

<section class="card card--harbor">
  <div class="brand">
    <div class="brand__name">Harbor Quill</div>
    <div class="brand__tagline">Multilingual Web Content and Language Services</div>
  </div>
  <div class="details">
    <p class="person"><span class="person__name">YOUR NAME</span><span class="person__sep">/</span><span class="person__title">Title</span></p>
    <ul class="contacts">
      <li><svg><use href="#icon-phone"/></svg>123-456-7890</li>
      <li><svg><use href="#icon-mobile"/></svg>123-456-7890</li>
      <li><svg><use href="#icon-fax"/></svg>123-456-7890</li>
      <li><svg><use href="#icon-mail"/></svg>name@website.com</li>
      <li><svg><use href="#icon-web"/></svg>www.harborquill-example.com</li>
    </ul>
    <p class="address">Complex name, Street<br>City, State, zip code</p>
  </div>
  <div class="bands"><span class="bands__primary"></span><span class="bands__secondary"></span></div>
  <p class="footnote">xxxxxxxxxxxxxxxxxxxxxxxxxxxxxxxxxxxxxxxxxxxxxxxxx</p>
</section>

<section class="card card--velmaro">
  <div class="brand">
    <div class="brand__name">Velmaro</div>
    <div class="brand__tagline">Search Visibility Consulting</div>
  </div>
  <div class="details">
    <p class="person"><span class="person__name">YOUR NAME</span><span class="person__sep">/</span><span class="person__title">Title</span></p>
    <ul class="contacts">
      <li><svg><use href="#icon-phone"/></svg>123-456-7890</li>
      <li><svg><use href="#icon-mobile"/></svg>123-456-7890</li>
      <li><svg><use href="#icon-fax"/></svg>123-456-7890</li>
      <li><svg><use href="#icon-mail"/></svg>name@website.com</li>
      <li><svg><use href="#icon-web"/></svg>www.velmaro-example.com</li>
    </ul>
    <p class="address">Complex name, Street<br>City, State, zip code</p>
  </div>
  <div class="bands"><span class="bands__primary"></span><span class="bands__secondary"></span></div>
  <p class="footnote">xxxxxxxxxxxxxxxxxxxxxxxxxxxxxxxxxxxxxxxxxxxxxxxxx</p>
</section>

</body>
</html>
```